Simple and Clean business card design

We would like the design to be simple clean and to incorporate our colors.

We are open to your design and talent, we have the dots in our logo as we think of it as data points and we connect data points for people.

We are open to see the great creative and clean design you bring to the table

Contact Information for Business Card

please include: name, position, email, phone and website

Font styles to use
Sans Serif

Requirements
Must have
• my colors incorporated, simplicity
Nice to have
• lots of white space, simplicity
Should not have
• complexicity/ complex art

```html
<!DOCTYPE html>
<html lang="en">
<head>
<meta charset="utf-8">
<title>Tessel business card</title>
<link rel="stylesheet" href="https://fonts.googleapis.com/css2?family=Poppins:wght@400;500;600;700&display=swap">
<style>
  :root {
    --backdrop: #868583;
    --ink: #0b0b0b;
    --paper: #ffffff;
    --blue: #5b87c7;
    --green: #34a853;
    --yellow: #f5c518;
    --red: #ea4335;
  }
  * { box-sizing: border-box; margin: 0; padding: 0; }
  html, body {
    width: 1200px; height: 900px; overflow: hidden;
    background: var(--backdrop);
    font-family: "Poppins", sans-serif;
  }
  .card {
    position: absolute;
    width: 540px; height: 310px;
    border-radius: 14px;
    box-shadow: 0 6px 18px rgba(0,0,0,0.25);
  }
  .card--front { left: 60px; top: 110px; background: var(--ink); }
  .card--back { left: 600px; top: 480px; background: var(--paper); }

  .wordmark {
    display: flex; align-items: center;
    font-weight: 600; letter-spacing: -1px; line-height: 1;
  }
  .wordmark__dot { border-radius: 50%; background: var(--green); flex: none; }

  .card--front .wordmark {
    position: absolute; left: 0; right: 0; top: 92px;
    justify-content: center; gap: 18px;
    color: var(--paper); font-size: 104px;
  }
  .card--front .wordmark__dot { width: 40px; height: 40px; }
  .front-url {
    position: absolute; left: 0; right: 0; top: 232px;
    text-align: center; font-size: 17px; font-weight: 500; letter-spacing: 0.5px;
  }
  .front-url .u-www { color: var(--blue); }
  .front-url .u-name { color: var(--red); }
  .front-url .u-tld { color: var(--green); }

  .card--back .wordmark {
    position: absolute; left: 40px; top: 180px;
    gap: 10px; color: var(--ink); font-size: 54px;
  }
  .card--back .wordmark__dot { width: 22px; height: 22px; }
  .divider {
    position: absolute; left: 262px; top: 60px;
    width: 1.5px; height: 130px; background: var(--ink);
  }
  .details { position: absolute; left: 290px; top: 52px; }
  .details__company { font-weight: 700; font-size: 22px; color: var(--ink); line-height: 1.1; }
  .details__role { font-size: 17px; color: var(--blue); margin-bottom: 12px; }
  .contact { list-style: none; }
  .contact__item {
    display: flex; align-items: center; gap: 9px;
    font-size: 15px; color: var(--ink); line-height: 1.7;
  }
  .contact__icon { width: 15px; height: 15px; flex: none; }
</style>
</head>
<body>

<section class="card card--front" aria-label="Card front">
  <div class="wordmark"><span class="wordmark__dot"></span><span>Tessel</span></div>
  <p class="front-url"><span class="u-www">www.</span><span class="u-name">Tessel</span><span class="u-tld">.one</span></p>
</section>

<section class="card card--back" aria-label="Card back">
  <div class="wordmark"><span class="wordmark__dot"></span><span>Tessel</span></div>
  <div class="divider"></div>
  <div class="details">
    <p class="details__company">Tessel.One</p>
    <p class="details__role">Founder/ CEO</p>
    <ul class="contact">
      <li class="contact__item">
        <svg class="contact__icon" viewBox="0 0 16 16" aria-hidden="true"><path fill="var(--green)" d="M3.5 1.5l2.5 0 1 3.5-1.8 1.2a8 8 0 0 0 4.6 4.6L11 9l3.5 1v2.5c0 1-1 2-2 2C6.5 14.5 1.5 9.5 1.5 3.5c0-1 1-2 2-2z"/></svg>
        555-014-2290
      </li>
      <li class="contact__item">
        <svg class="contact__icon" viewBox="0 0 16 16" aria-hidden="true"><rect x="1" y="3" width="14" height="10" rx="1" fill="var(--yellow)"/><path d="M1.5 3.5L8 9l6.5-5.5" fill="none" stroke="#fff" stroke-width="1.3"/></svg>
        nora.vale@tessel.one
      </li>
      <li class="contact__item">
        <svg class="contact__icon" viewBox="0 0 16 16" aria-hidden="true"><circle cx="8" cy="8" r="7" fill="var(--red)"/><path d="M1 8h14M8 1c-3 3.5-3 10.5 0 14M8 1c3 3.5 3 10.5 0 14" fill="none" stroke="#fff" stroke-width="1"/></svg>
        www.Tessel.one
      </li>
    </ul>
  </div>
</section>

</body>
</html>
```